Web design for facial expression recognition service

We offer a service which allows customers to film large panels of participants looking at some video/screen (e.g. an advertisement) and to analyze the facial expressions shown by the participants. We are looking for the design of a new website which will make it easy for our customers to setup and view the results of these experiments online.
Competitor's websites that may serve as a reference are:
http://www.moriventa.com/quelbo/#pane_overview
http://www.dunvarpix.com/homepage.aspx
https://www.tamlora.com/
The website will (for as far as the design is concerned) consist of three parts:
- A public home page (and perhaps some contact/news/about page), designed to catch the attention/interest potential customers.
- A (protected) project result page, showing the results in an interactive page with charts and numerical data.
- Pages (also protected) with fields and tables (setting up the project details).
The winner of this design project should provide us with at least one design for each of the above in order to get a complete 'theme' going which our developers can use. However, you are welcome to initially only provide the design for the project result page and/or home page.
We are looking for a modern, fresh, yet professional look (my client is a more established party in the field).
The final delivery should consist of layered Photoshop or Illustrator files.
Thank you in advance for participating!
Updates
Dear designers,
Project Deadline Extended
Reason: Extending the deadline by a few days to give designers a chance to submit designs for the other pages and process further feedback.
Target Market(s)
marketing research agencies (B2B service)
Requirements
Must have
- Home page:
- Basic advertisement of the service; some quick explanation of how it works
- A way to login for existing users
- A link/button/banner inviting people to sign up
- Navigation controls to 2-3 other pages
- Social media links (Facebook, LinkedIn group)
- Company logo (sorry, can't provide it as my client wishes to remain anonymous for now, but it's rounded and has blue as it's main color).
- Copyright / creator details
Project result page:
(see attachment 1 for a functional mockup - the design may follow this layout closely, or be completely different)
- Title
- A video player and basic numerical data
- Different views of the analysis results can dynamically be added/removed/collapsed/expanded; each one of these views will show some kind of chart, filters (combos), numerical data and a download button/link.
- A way to sign out, go to the main project page and go to the main page
- Logo
- Copyright
The form pages:
(see attachment 2 for a functional mockup of one of the pages; feel free to change some elements to better show the overall style)
- Title
- Text fields, combos, calendar pickers, tables, navigation links
- Logo
- Copyright
Nice to have
- Any creative text elements or product logo/symbol are a bonus. However, the basic "Lorem Ipsum" would do too.

```html
<!DOCTYPE html>
<html lang="en">
<head>
<meta charset="utf-8">
<title>Korvelden — Facial Recognition Analysis</title>
<link href="https://fonts.googleapis.com/css2?family=Source+Sans+3:wght@400;600;700&family=Arimo:wght@400;700&display=swap" rel="stylesheet">
<style>
:root{
  --blue:#1a78d6;
  --blue-deep:#0d5fb8;
  --blue-light:#3a9ae6;
  --link-blue:#3aa0e0;
  --ink:#111;
  --text:#444;
  --muted:#555;
  --panel:#f1f1f1;
  --orange:#f7a81a;
  --orange-deep:#f58a0c;
  --white:#fff;
}
*{margin:0;padding:0;box-sizing:border-box}
html,body{width:960px;height:1200px;overflow:hidden;background:var(--panel)}
body{position:relative;font-family:"Arimo",Arial,sans-serif;color:var(--text)}
.abs{position:absolute}

/* hero */
.hero{left:0;top:0;width:960px;height:574px;
  background:radial-gradient(ellipse at 55% 45%,var(--blue-light) 0%,var(--blue) 45%,var(--blue-deep) 100%)}
.header-band{left:0;top:104px;width:960px;height:35px;
  background:linear-gradient(to bottom,rgba(0,0,0,0),rgba(0,30,80,.18))}
.top-edge{left:0;top:0;width:960px;height:8px;background:var(--ink)}
.utility{left:680px;top:0;width:280px;height:30px;background:var(--ink);
  clip-path:polygon(0 0,100% 0,100% 100%,8% 100%)}
.utility-links{left:711px;top:8px;font:700 9px "Arimo",Arial,sans-serif;color:var(--link-blue);letter-spacing:.2px}
.utility-links span{margin:0 10px}

.brand-name{left:96px;top:52px;font:700 28px/34px "Source Sans 3",sans-serif;color:var(--white);letter-spacing:.5px}

.nav{left:418px;top:53px;width:542px;height:33px;background:linear-gradient(#fff,#e6e6e6)}
.nav a{font:700 11px "Arimo",Arial,sans-serif;color:var(--muted);text-decoration:none;position:absolute;top:11px}
.nav .home{left:0;top:0;width:78px;height:33px;background:var(--ink);color:var(--white);border-radius:6px 0 0 6px;text-align:center;line-height:33px}

.monitor{left:104px;top:198px;width:350px;height:294px;border-radius:8px;
  background:linear-gradient(to bottom,#1a1a1a 0%,#1a1a1a 79%,#cfcfcf 80%,#e8e8e8 100%);
  clip-path:polygon(0 0,100% 0,100% 80%,65% 80%,67% 100%,33% 100%,35% 80%,0 80%)}
.screen{left:117px;top:212px;width:322px;height:201px;background:linear-gradient(90deg,#bcd7ea,#8a7464 40%,#c9a88e 55%,#6d5544 80%,#bcd7ea)}

.headline{left:469px;top:224px;font:600 29px/35px "Source Sans 3",sans-serif;color:var(--white);text-shadow:0 1px 2px rgba(0,0,0,.35)}
.sub{left:474px;top:317px;width:394px;font:400 18.5px/23px "Source Sans 3",sans-serif;color:var(--white);text-align:justify;text-shadow:0 1px 2px rgba(0,0,0,.35);letter-spacing:.3px}
.cta{left:472px;top:414px;width:208px;height:36px;border-radius:18px;
  background:linear-gradient(#fbb82c,var(--orange-deep));color:var(--white);
  font:600 15px/36px "Source Sans 3",sans-serif;text-align:center;text-shadow:0 1px 1px rgba(0,0,0,.3)}
.dots{left:458px;top:541px;display:flex;gap:6px}
.dots i{width:10px;height:10px;border-radius:50%;background:#ddd;display:block}
.dots i.on{background:#0c4f93}

/* how it works */
.section-title{font:700 15px "Source Sans 3",sans-serif;color:#444}
.how-title{left:0;top:585px;width:960px;text-align:center}
.hatch{left:96px;top:618px;width:766px;height:5px;
  background:repeating-linear-gradient(90deg,#c9c9c9 0 1px,transparent 1px 3px)}
.steps{left:0;top:640px}
.step-text{width:220px;text-align:center;font:600 10.5px/19px "Source Sans 3",sans-serif;color:#444}

/* lower */
.lower-shade{left:0;top:810px;width:960px;height:30px;background:linear-gradient(rgba(0,0,0,0),rgba(0,0,0,.05))}
.lower{left:0;top:838px;width:960px;height:282px;background:var(--panel)}
.rule{height:1px;background:#d6d6d6}
.video{left:96px;top:898px;width:254px;height:188px;background:radial-gradient(ellipse at 50% 40%,#2a5fae 0%,#0a1a3a 35%,#000 70%)}
.video-bar{left:96px;top:1070px;width:254px;height:16px;background:#141414;border-top:2px solid #444}
.welcome{left:375px;top:893px;width:488px;font:400 9.6px/19.2px "Arimo",Arial,sans-serif;color:#444;text-align:justify}
.welcome p+p{margin-top:19.2px}

/* footer */
.footer{left:0;top:1120px;width:960px;height:80px;background:var(--ink)}
.copy{left:96px;top:1150px;font:400 9.6px "Arimo",Arial,sans-serif;color:var(--white)}
.social{top:1147px;width:26px;height:26px;border-radius:50%}
</style>
</head>
<body>

<div class="abs hero"></div>
<div class="abs header-band"></div>
<div class="abs top-edge"></div>
<div class="abs utility"></div>
<div class="abs utility-links">SITEMAP<span>|</span>HELP<span>|</span>LOGIN</div>

<div class="abs brand-name">KORVELDEN</div>

<nav class="abs nav">
  <a class="home" href="#">HOME</a>
  <a href="#" style="left:88px">CLIENTS</a>
  <a href="#" style="left:167px">PRESS</a>
  <a href="#" style="left:236px">TEAM</a>
  <a href="#" style="left:299px">JOBS</a>
  <a href="#" style="left:360px">CONTACT US</a>
</nav>

<div class="abs monitor" role="img" aria-label="Desktop monitor showing facial recognition analysis"></div>
<div class="abs screen" role="img" aria-label="Screen with a person's portrait being analysed"></div>

<h1 class="abs headline">WE ARE A FACIAL RECOGNITION<br>ANALYSIS COMPANY.</h1>
<p class="abs sub">We make group of 10 users see a video and analyse their facial expressions.</p>
<a class="abs cta">SIGN UP TO KNOW MORE</a>
<div class="abs dots"><i></i><i></i><i class="on"></i></div>

<h2 class="abs section-title how-title">HOW IT WORKS</h2>
<div class="abs hatch"></div>

<svg class="abs steps" width="960" height="100" viewBox="0 640 960 100">
  <defs>
    <linearGradient id="stepFill" x1="0" y1="0" x2="0" y2="1">
      <stop offset="0" stop-color="#fbbf2a"/><stop offset="1" stop-color="#f6920e"/>
    </linearGradient>
  </defs>
  <g fill="none" stroke="#222" stroke-width="0.9" stroke-dasharray="3 2">
    <path d="M253 690 Q349 610 445 690 Q349 770 253 690Z"/>
    <path d="M514 690 Q609 610 705 690 Q609 770 514 690Z"/>
  </g>
  <g fill="url(#stepFill)">
    <circle cx="218" cy="689" r="32"/><circle cx="479" cy="689" r="32"/><circle cx="738" cy="689" r="32"/>
  </g>
  <g fill="#fff" font-family="Source Sans 3, sans-serif" font-weight="400" font-size="28" text-anchor="middle">
    <text x="217" y="699">1</text><text x="479" y="699">2</text><text x="738" y="699">3</text>
  </g>
</svg>

<p class="abs step-text" style="left:108px;top:762px">Lorem ipsum dolor sit amet, consectetur<br>adipisicing elit, sed do</p>
<p class="abs step-text" style="left:369px;top:756px">Lorem ipsum dolor sit amet, consectetur<br>adipisicing elit, sed do</p>
<p class="abs step-text" style="left:625px;top:762px">Lorem ipsum dolor sit amet, consectetur<br>adipisicing elit, sed do</p>

<div class="abs lower-shade"></div>
<div class="abs lower"></div>

<h2 class="abs section-title" style="left:94px;top:855px">OUR VIDEO</h2>
<div class="abs rule" style="left:96px;top:882px;width:256px"></div>
<h2 class="abs section-title" style="left:375px;top:855px">WELCOME!</h2>
<div class="abs rule" style="left:375px;top:882px;width:489px"></div>

<div class="abs video" role="img" aria-label="Company video with animated title"></div>
<div class="abs video-bar"></div>

<div class="abs welcome">
  <p>Sed ut perspiciatis unde omnis iste natus error sit voluptatem accusantium doloremque laudantium, totam rem aperiam, eaque ipsa quae ab illo inventore veritatis et quasi architecto beatae vitae dicta sunt explicabo. Nemo enim ipsam voluptatem quia voluptas sit aspernatur aut odit aut fugit, sed quia consequuntur magni dolores eos qui ratione voluptatem sequi nesciunt.</p>
  <p>Neque porro quisquam est, qui dolorem ipsum quia dolor sit amet, consectetur, adipisci velit, sed quia non numquam eius modi tempora incidunt ut labore et dolore magnam aliquam quaerat voluptatem. Ut enim ad minima veniam, quis nostrum exercitationem ullam corporis suscipit laboriosam, nisi ut aliquid ex ea commodi consequatur? Quis autem vel eum iure reprehenderit qui in ea voluptate velit esse quam nihil molestiae consequatur, vel illum qui dolorem eum fugiat quo voluptas nulla pariatur</p>
</div>

<footer class="abs footer"></footer>
<div class="abs copy">© 2013 Korvelden, Inc. All rights reserved</div>
<a class="abs social" style="left:806px;background:#3b5b9a" aria-label="Social network link"></a>
<a class="abs social" style="left:838px;background:#1a7bb8" aria-label="Professional network group link"></a>

</body>
</html>
```